Creation of a construction/bricklaying business website

Following the template format of "Halloway 7", the following content would need to be included:
1. Landing page with 3 tiles that go to their own pages.
- Landing page to include background photo and description of services offered.
2. 3 tiles to include:
a) "Contact Us For A Free Quote or Friendly Discussion" Form (middle tile)
b) Case Studies and Testimonials
c) Certifications and Professional Membership
- Design logo to be used from previous SketchNestle project. Example of logo attached below, please access full JPG files from our account.

Target Market(s)

Prospective clients seeking construction work (bricklaying speciality)

Industry/Entity Type

Residential Construction

Coding

Coded - Design and coding required

Number of Pages Required

4 page

Font styles to use
Sans Serif

Colors

Designer to choose colors to be used in the design.

Requirements
Must have
• Following the template format of "Halloway 7", the following content would need to be included:
• 1. Landing parent page with 3 tiles that go to the 3 child pages.
• - Landing page to include background photo and description of services offered.
• 2. 3 tiles to include:
• a) "Contact Us For A Free Quote or Friendly Discussion" Form (middle tile)
• b) Case Studies and Testimonials (first tile / left side)
• c) Certifications and Professional Memberships (third tile / right side) (This should include logos of the relevant organisations being displayed. Specifically GQT and the Pillar Seal GQT).
• - Design logo to be used from previous SketchNestle project. Example of logo attached below, please access full JPG files from our account.
Nice to have
• Sleek and modern feel.
• Approachable in terms of how people can contact the company for a quote.
• Traditional pictures to give credibility and comfort around choosing this company.
Should not have
• Cheesy pictures
• Over-complicated
• Simple to use
• Easy URL domain name

```html
<!DOCTYPE html>
<html lang="en">
<head>
<meta charset="utf-8">
<title>R.T.Harlow Construction Ltd</title>
<link href="https://fonts.googleapis.com/css2?family=Arimo:wght@400;500;600;700&family=Jost:wght@400;500&display=swap" rel="stylesheet">
<style>
:root{
  --blue:#0f5aa8;
  --blue-dark:#0b4a8c;
  --ink:#222a30;
  --icon:#2f3338;
  --text:#1d1d1d;
  --tile:#e8ecee;
  --white:#ffffff;
  --badge:#c8102e;
}
*{margin:0;padding:0;box-sizing:border-box}
html,body{width:920px;height:1200px;overflow:hidden;background:var(--white)}
body{position:relative;font-family:"Jost",sans-serif;color:var(--text)}
.abs{position:absolute}

.hero{left:0;top:0;width:920px;height:315px;background:linear-gradient(100deg,#5a3a30 0%,#7a4a3a 30%,#6b4539 55%,#4b4440 80%,#6a6a68 100%)}
.hero-shade{left:0;top:0;width:920px;height:315px;background:linear-gradient(180deg,rgba(0,0,0,.25),rgba(0,0,0,.1) 50%,rgba(0,0,0,.25))}
.contact-item{display:flex;align-items:center;gap:8px;color:var(--white);font-size:11.5px;line-height:16px;font-weight:400}
.contact-item .icon{width:28px;height:28px;border-radius:50%;background:var(--blue);display:flex;align-items:center;justify-content:center;flex:none}
.brand{left:0;width:920px;text-align:center;color:var(--white);font-family:"Arimo",sans-serif;font-weight:700}
.brand-name{top:128px;font-size:50px;letter-spacing:-1px;line-height:56px}
.brand-sub{top:182px;font-size:17px;letter-spacing:3px;line-height:20px}

.main-nav{left:0;top:315px;width:917px;height:36px;background:var(--blue);font-family:"Arimo",sans-serif;font-weight:600;font-size:11px}
.main-nav a{color:var(--white);text-decoration:none;position:absolute;top:11px}
.main-nav a.current{color:#0b1c30}

.about-title{top:380px;left:0;width:920px;text-align:center;color:var(--blue);font-family:"Arimo",sans-serif;font-weight:700;font-size:21px}
.about-lead{top:422px;left:0;width:920px;text-align:center;font-family:"Arimo",sans-serif;font-weight:600;font-size:14.5px;line-height:18px;letter-spacing:.4px;color:var(--ink)}

.service{width:120px;text-align:center;top:482px}
.service .disc{width:78px;height:78px;margin:0 auto;border-radius:50%;border:2.5px solid var(--blue);background:radial-gradient(circle at 50% 40%,#fafafa,#e2e4e6);display:flex;align-items:center;justify-content:center;box-shadow:0 7px 5px -5px rgba(0,0,0,.18)}
.service .label{margin-top:22px;font-family:"Arimo",sans-serif;font-weight:600;font-size:14.5px;line-height:17.5px;color:var(--ink)}

.intro{left:124px;width:672px;text-align:center;font-size:12px;line-height:18.5px;color:var(--text)}

.tile{top:754px;width:224px;height:208px;text-align:center}
.tile.grey{background:var(--tile)}
.tile .art{margin:22px auto 0;height:50px;display:flex;justify-content:center}
.tile h3{margin-top:10px;font-family:"Arimo",sans-serif;font-weight:600;font-size:10.5px;line-height:14.5px;color:var(--ink)}
.tile p{margin-top:10px;font-size:10px;line-height:16.5px;padding:0 6px;color:var(--text)}
.tile a{display:block;margin-top:12px;font-family:"Arimo",sans-serif;font-weight:600;font-size:11px;color:var(--blue);text-decoration:none}
.badge{width:29px;height:48px;background:var(--badge);border-radius:2px}

.footer{left:0;top:1008px;width:920px;height:192px;background:linear-gradient(160deg,#2a3a4c 0%,#1a2b3d 45%,#223244 70%,#2d3a3a 100%)}
.footer-brand{left:0;top:1036px;width:920px;text-align:center;color:var(--white);font-family:"Arimo",sans-serif;font-weight:700}
.footer-brand .n{font-size:19px;line-height:20px}
.footer-brand .s{font-size:7px;letter-spacing:1.5px;line-height:9px}
.rule{left:146px;top:1146px;width:628px;height:1px;background:rgba(255,255,255,.15)}
.copyright{left:146px;top:1169px;font-size:10.5px;color:var(--white)}
.social{top:1164px;width:24px;height:24px;border-radius:50%;background:var(--white)}
</style>
</head>
<body>

<div class="abs hero" role="img" aria-label="Photograph of a new red brick garden wall outside terraced houses with bricklaying tools"></div>
<div class="abs hero-shade"></div>

<div class="abs contact-item" style="left:124px;top:14px">
  <span class="icon"><svg width="14" height="14" viewBox="0 0 24 24"><path fill="#fff" d="M6.6 10.8a15.1 15.1 0 0 0 6.6 6.6l2.2-2.2c.3-.3.7-.4 1-.2 1.1.4 2.3.6 3.6.6.6 0 1 .4 1 1V20c0 .6-.4 1-1 1A17 17 0 0 1 3 4c0-.6.4-1 1-1h3.5c.6 0 1 .4 1 1 0 1.3.2 2.5.6 3.6.1.3 0 .7-.2 1z"/></svg></span>
  <span>Call Us On<br>123.456.7890</span>
</div>
<div class="abs contact-item" style="left:626px;top:13px">
  <span class="icon"><svg width="15" height="12" viewBox="0 0 24 18"><rect x="1" y="1" width="22" height="16" fill="none" stroke="#fff" stroke-width="2"/><path d="M1 1l11 9 11-9" fill="none" stroke="#fff" stroke-width="2"/></svg></span>
  <span>Email Us On<br>info@rtharlowbuild.com</span>
</div>

<div class="abs brand brand-name">R.T.Harlow</div>
<div class="abs brand brand-sub">CONSTRUCTION LTD</div>

<nav class="abs main-nav">
  <a class="current" href="#" style="left:133px">Home</a>
  <a href="#" style="left:200px">Case Studies &amp; Testimonials</a>
  <a href="#" style="left:386px">Contact Us For A Free Quote</a>
  <a href="#" style="left:580px;top:10px">Certifications &amp; Professional Memberships</a>
</nav>

<h1 class="abs about-title">About Us</h1>
<p class="abs about-lead">R.T.Harlow Construction Ltd is a construction company that has expertise and<br>experience in the following areas</p>

<div class="abs service" style="left:103px"><div class="disc">
  <svg width="44" height="44" viewBox="0 0 48 48" fill="none" stroke="var(--icon)" stroke-width="2" stroke-linejoin="round">
    <path d="M6 22L20 10l14 12"/><path d="M9 20v16h22V20"/><rect x="13" y="24" width="6" height="6"/><rect x="23" y="24" width="5" height="12"/>
    <path d="M34 22h8v14h-8" stroke-dasharray="2 2"/><path d="M8 41h34M8 41l3-2M8 41l3 2M42 41l-3-2M42 41l-3 2" stroke-width="1.4"/>
  </svg></div><div class="label">Extensions</div></div>
<div class="abs service" style="left:221px"><div class="disc">
  <svg width="44" height="44" viewBox="0 0 48 48" fill="none" stroke="var(--icon)" stroke-width="3" stroke-linejoin="round">
    <path d="M5 24L24 7l19 17"/><path d="M10 20v20h28V20"/><path d="M33 9v7" stroke-width="4"/>
    <rect x="15" y="25" width="7" height="7" fill="var(--icon)" stroke="none"/><rect x="26" y="26" width="7" height="14" fill="var(--icon)" stroke="none"/>
  </svg></div><div class="label">New build /<br>New houses</div></div>
<div class="abs service" style="left:346px"><div class="disc">
  <svg width="46" height="46" viewBox="0 0 48 48" fill="var(--icon)">
    <rect x="6" y="8" width="36" height="3"/>
    <rect x="6" y="13" width="10" height="5"/><rect x="18" y="13" width="10" height="5"/><rect x="30" y="13" width="12" height="5"/>
    <rect x="6" y="20" width="5" height="5"/><rect x="13" y="20" width="10" height="5"/><rect x="25" y="20" width="10" height="5"/><rect x="37" y="20" width="5" height="5"/>
    <rect x="6" y="27" width="10" height="5"/><rect x="18" y="27" width="10" height="5"/><rect x="30" y="27" width="12" height="5"/>
    <rect x="6" y="34" width="5" height="5"/><rect x="13" y="34" width="10" height="5"/><rect x="25" y="34" width="10" height="5"/><rect x="37" y="34" width="5" height="5"/>
  </svg></div><div class="label">Garden walls</div></div>
<div class="abs service" style="left:458px"><div class="disc">
  <svg width="44" height="44" viewBox="0 0 48 48" fill="none" stroke="var(--icon)" stroke-width="2">
    <rect x="6" y="8" width="30" height="30"/><path d="M6 15h30M6 23h30M6 31h30M16 8v7M26 8v7M11 15v8M21 15v8M31 15v8M16 23v8M26 23v8M11 31v7M21 31v7"/>
    <path d="M24 40l12-14 6 4-10 14z" fill="#e8eaec"/><path d="M36 26l7-10" stroke-width="3"/>
  </svg></div><div class="label">Plastering</div></div>
<div class="abs service" style="left:578px"><div class="disc">
  <svg width="44" height="44" viewBox="0 0 48 48" fill="var(--icon)">
    <rect x="10" y="6" width="3" height="10"/><path d="M6 16h11l-5 14z"/>
    <rect x="18" y="24" width="10" height="4"/><rect x="30" y="24" width="12" height="4"/>
    <rect x="14" y="31" width="12" height="4"/><rect x="28" y="31" width="14" height="4"/>
    <rect x="10" y="38" width="14" height="4"/><rect x="26" y="38" width="16" height="4"/>
  </svg></div><div class="label">Brickwork</div></div>
<div class="abs service" style="left:698px"><div class="disc">
  <svg width="44" height="44" viewBox="0 0 48 48" fill="var(--icon)">
    <rect x="8" y="5" width="10" height="3"/><rect x="11.5" y="7" width="3" height="18"/><path d="M7 24h12v12a6 6 0 0 1-12 0z"/>
    <path d="M20 42l8-12 5 4 4-3 7 11z"/><circle cx="40" cy="33" r="2"/><circle cx="36" cy="28" r="1.5"/>
  </svg></div><div class="label">Groundworks</div></div>

<p class="abs intro" style="top:645px">We pride ourselves on attention to detail, pride in our completed project and client satisfaction. We believe in full transparency and this is reflected in the jobs we quote for you. We break down each step with both labour and materials cost so you can see exactly what you are paying for.</p>
<p class="abs intro" style="top:713px">Feel free to get in touch and we can talk through what you are looking to achieve.</p>

<section class="abs tile grey" style="left:124px">
  <div class="art">
    <svg width="74" height="50" viewBox="0 0 74 50" fill="none" stroke="var(--blue-dark)" stroke-width="2">
      <rect x="30" y="2" width="38" height="44" rx="2" fill="#fff"/>
      <path d="M35 9h28" stroke-width="2.5"/>
      <circle cx="49" cy="25" r="8" fill="#fff"/><path d="M55 31l8 8" stroke-width="3"/>
      <path d="M45 24h8M45 27h8" stroke="var(--icon)" stroke-width="1.5"/>
      <rect x="40" y="34" width="12" height="10" fill="var(--icon)" stroke="none"/>
      <ellipse cx="14" cy="34" rx="12" ry="9" fill="var(--blue)" stroke="none"/><path d="M8 41l-4 6 9-4" fill="var(--blue)" stroke="none"/>
      <ellipse cx="28" cy="30" rx="6" ry="5" fill="#9aa3ab" stroke="none"/>
    </svg>
  </div>
  <h3>Case Studies and<br>Testimonials</h3>
  <p>Ut wisi enim ad minim veniam, quis nostrud exerci tation ullamcorper suscipit lobortis nisl ut aliquip ex ea commodo consequat.</p>
  <a href="#">Read More</a>
</section>
<section class="abs tile" style="left:348px">
  <div class="art">
    <svg width="50" height="50" viewBox="0 0 50 50" fill="none" stroke="var(--blue)" stroke-width="2.2" stroke-linejoin="round">
      <path d="M10 3h24l10 10v34H10z"/><path d="M34 3v10h10"/>
      <path d="M20 22h18M20 27h18M20 32h18"/>
      <path d="M14 10c0 4 3 7 6 8l1.5-2" stroke-width="2"/>
      <path d="M4 38l4 7 8-16" stroke="var(--icon)" stroke-width="3"/>
    </svg>
  </div>
  <h3>Contact Us For A<br>Free Quote</h3>
  <p>Ut wisi enim ad minim veniam, quis nostrud exerci tation ullamcorper suscipit lobortis nisl ut aliquip ex ea commodo consequat.</p>
  <a href="#">Contact Us</a>
</section>
<section class="abs tile grey" style="left:572px">
  <div class="art" style="gap:6px">
    <div class="badge" role="img" aria-label="GQT membership badge"></div>
    <div class="badge" role="img" aria-label="Pillar Seal GQT badge"></div>
  </div>
  <h3>Certifications and Professional<br>Memberships</h3>
  <p>Ut wisi enim ad minim veniam, quis nostrud exerci tation ullamcorper suscipit lobortis nisl ut aliquip ex ea commodo consequat.</p>
  <a href="#">Know More</a>
</section>

<footer>
  <div class="abs footer" role="img" aria-label="Darkened aerial photograph of a city skyline"></div>
  <div class="abs footer-brand"><div class="n">R.T.Harlow</div><div class="s">CONSTRUCTION LTD</div></div>

  <div class="abs contact-item" style="left:146px;top:1086px">
    <span class="icon"><svg width="12" height="15" viewBox="0 0 24 30"><path fill="#fff" d="M12 0a10 10 0 0 0-10 10c0 7.5 10 20 10 20s10-12.5 10-20A10 10 0 0 0 12 0zm0 14a4 4 0 1 1 0-8 4 4 0 0 1 0 8z"/></svg></span>
    <span>Street Name, City Name<br>State Zipcode</span>
  </div>
  <div class="abs contact-item" style="left:392px;top:1087px">
    <span class="icon"><svg width="14" height="14" viewBox="0 0 24 24"><path fill="#fff" d="M6.6 10.8a15.1 15.1 0 0 0 6.6 6.6l2.2-2.2c.3-.3.7-.4 1-.2 1.1.4 2.3.6 3.6.6.6 0 1 .4 1 1V20c0 .6-.4 1-1 1A17 17 0 0 1 3 4c0-.6.4-1 1-1h3.5c.6 0 1 .4 1 1 0 1.3.2 2.5.6 3.6.1.3 0 .7-.2 1z"/></svg></span>
    <span>Call Us On :<br>123.456.7890</span>
  </div>
  <div class="abs contact-item" style="left:596px;top:1087px">
    <span class="icon"><svg width="15" height="12" viewBox="0 0 24 18"><rect x="1" y="1" width="22" height="16" fill="none" stroke="#fff" stroke-width="2"/><path d="M1 1l11 9 11-9" fill="none" stroke="#fff" stroke-width="2"/></svg></span>
    <span>Email<br>info@rtharlowbuild.com</span>
  </div>

  <div class="abs rule"></div>
  <p class="abs copyright">Copyright ©2018 R.T.Harlow Construction Ltd. All Rights Reserved.</p>
  <span class="abs social" style="left:661px" aria-label="Social link"></span>
  <span class="abs social" style="left:688px" aria-label="Social link"></span>
  <span class="abs social" style="left:714px" aria-label="Social link"></span>
  <span class="abs social" style="left:742px" aria-label="Social link"></span>
</footer>

</body>
</html>
```